Post Card Design

I need a post card design for an Educational Program - targeted at professionals and people interested in self development and awareness. The PDF file attached is an example of the program being offered at another company "The Brightwater Studio" The Tree Logo and The Brightwater Studio can NOT be used as this program maybe offered at places other than The Brightwater Studio . A blank spot should be left where I will use a separate sticker to indicate the time and location of the next course. The MAIN Title text will be "RESOLVE AND RENEWAL" instead of "Harmony Growth Workshop "HGW"
I am attaching my own logo. The image of the Sun and the Pathway should be used. DO NOT use the Logo text "SerenityMeadows or name and tagline. The image of the Sun and the pathway could be used as a watermark background filling the whole of one side of the card. I am attaching an image of me that should go in a small place. I will need to edit text and content myself after I choose the design. I would like one with rounded corners

```html
<!DOCTYPE html>
<html lang="en">
<head>
<meta charset="utf-8">
<title>Resolve and Renewal – Post Card</title>
<link href="https://fonts.googleapis.com/css2?family=Source+Sans+3:wght@400;700&display=swap" rel="stylesheet">
<style>
  :root {
    --brand-blue: #31a6da;
    --ink: #111111;
    --paper: #ffffff;
    --sticker-border: #a4a4a4;
  }
  * { box-sizing: border-box; margin: 0; padding: 0; }
  html, body {
    width: 1200px; height: 929px; overflow: hidden;
    background: var(--paper);
  }
  .card {
    position: relative;
    width: 1200px; height: 929px;
    font-family: "Source Sans 3", Arial, sans-serif;
    color: var(--ink);
  }
  .card-frame {
    position: absolute;
    left: 34px; top: 34px; width: 1132px; height: 861px;
    border: 10px solid var(--brand-blue);
    border-radius: 46px;
    background: var(--paper);
    overflow: hidden;
  }
  .title-band {
    position: absolute;
    left: 0; top: 0; right: 0; height: 74px;
    background: var(--brand-blue);
    display: flex; align-items: center; justify-content: center;
  }
  .title {
    font-family: "Source Sans 3", Arial, sans-serif;
    font-weight: 700;
    font-size: 42px;
    letter-spacing: 6px;
    color: var(--paper);
    line-height: 1;
  }
  .intro {
    position: absolute;
    left: 72px; top: 133px; width: 396px;
    font-size: 20px; line-height: 29.8px;
  }
  .intro p + p { margin-top: 29.8px; }
  .intro .line { display: block; white-space: nowrap; }
  .intro .line.fill {
    white-space: normal;
    text-align: justify;
    text-align-last: justify;
  }
  .intro strong { font-weight: 700; }
  .about {
    position: absolute;
    left: 507px; top: 130px; width: 640px;
  }
  .about-heading {
    margin-left: 18px;
    font-size: 23px; font-weight: 700;
    line-height: 32px;
  }
  .about-list { list-style: none; }
  .about-list li {
    position: relative;
    padding-left: 18px;
    font-size: 21.5px; line-height: 32.6px;
    white-space: nowrap;
  }
  .about-list li::before {
    content: "";
    position: absolute; left: 0; top: 11px;
    border-left: 7px solid var(--brand-blue);
    border-top: 6px solid transparent;
    border-bottom: 6px solid transparent;
  }
  .sticker-space {
    position: absolute;
    left: 493px; top: 648px; width: 644px; height: 215px;
    border: 3px solid var(--sticker-border);
    display: flex; flex-direction: column;
    align-items: center; justify-content: center;
    font-size: 25px; line-height: 36px;
    text-align: center;
  }
</style>
</head>
<body>
  <div class="card">
    <div class="card-frame">
      <header class="title-band">
        <h1 class="title">RESOLVE AND RENEWAL</h1>
      </header>
    </div>

    <section class="intro">
      <p>
        <span class="line fill">Do you often feel stress in your life,</span>
        <span class="line fill">experience difficult emotions or feel</span>
        <span class="line fill">disconnected from others? Do you want</span>
        <span class="line fill">to increase your emotional strength and</span>
        <span class="line fill">cope better with stress? Do you find it</span>
        <span class="line fill">difficult to respond to the suffering or</span>
        <span class="line fill">demands of others? Do you often feel</span>
        <span class="line fill">critical of yourself or others? Do you</span>
        <span class="line fill">want to make a positive difference in the</span>
        <span class="line">world?</span>
      </p>
      <p>
        <span class="line">Did you answer YES to most of these</span>
        <span class="line">questions?</span>
        <span class="line fill">If so, our <strong>RESOLVE AND RENEWAL</strong></span>
        <span class="line fill">(RR) program could be a big help for</span>
        <span class="line">you.</span>
      </p>
      <p>
        <span class="line fill">RR program designed to help you to</span>
        <span class="line fill">develop the qualities of compassion,</span>
        <span class="line fill">empathy and kindness for yourself and</span>
        <span class="line fill">for others. RR program integrates</span>
        <span class="line fill">traditional contemplative practices with</span>
        <span class="line fill">contemporary psychology and scientific</span>
        <span class="line">research on compassion.</span>
      </p>
    </section>

    <section class="about">
      <h2 class="about-heading">ABOUT&nbsp; RR PROGRAM</h2>
      <ul class="about-list">
        <li>In our sessions, you can learn and practice tools and<br>techniques to help you improve your mood and have<br>more positive experiences in your life.</li>
        <li>You will receive instruction for visualizations, daily<br>meditations, and in - class interaction to help you<br>increase your confidence and improve relationships.</li>
        <li>Classes are held in downtown Toronto once a week for<br>8 weeks. Each class is 2 hours long.</li>
        <li>Our groups are small, no more than 10 participants. This<br>will ensure that you get the individual attention that you<br>need.</li>
        <li>RR is proven to support health, happiness and well-being.<br>The skills you learn with us will help you long after the<br>course has ended.</li>
      </ul>
    </section>

    <div class="sticker-space">
      <span>Sticker space</span>
      <span>3 x 1 inches</span>
    </div>
  </div>
</body>
</html>
```